DESIGN OF STATIONERY - TORVALE MED

WE WORK IN THE FIELD OF HEALTH (IMAGING: MRI - CT ETC.).
WE WOULD LIKE TO CREATE THE ENTIRE STATIONERY DESIGN : LETTERHEAD, BUSINESS CARD, CALENDAR, INVOICES, CD HOLDER, ETC.

Target Market(s)

PERSONS UNDERTAKING HEALTH EXAMINATIONS

```html
<!DOCTYPE html>
<html lang="en">
<head>
<meta charset="utf-8">
<title>Torvale Med – Stationery</title>
<link rel="stylesheet" href="https://fonts.googleapis.com/css2?family=Poppins:wght@400;500;600;700&family=Roboto:wght@400;500&display=swap">
<style>
  :root{
    --brand-blue:#1e6fbf;
    --brand-teal:#1a9a8a;
    --paper:#f8f8f8;
    --backdrop:#dedede;
    --ink:#3a3a3a;
    --ink-soft:#6b6b6b;
    --cross-tint:#dbe3e8;
    --photo-a:#dfe7ee;
    --photo-b:#9fb1c2;
  }
  *{box-sizing:border-box;margin:0;padding:0}
  html,body{width:1200px;height:900px;overflow:hidden}
  body{background:var(--backdrop);position:relative;font-family:"Roboto",Arial,sans-serif;color:var(--ink)}
  address{font-style:normal}
  .sheet{position:absolute;background:var(--paper);box-shadow:0 2px 6px rgba(0,0,0,.12);overflow:hidden}
  .brand{font-family:"Poppins",Arial,sans-serif;font-weight:600;color:var(--brand-blue);display:flex;align-items:center;gap:6px;letter-spacing:.5px;white-space:nowrap}
  .brand::before{content:"";width:.7em;height:.7em;background:var(--brand-teal)}
  .footer-bands{position:absolute;left:0;bottom:0;width:100%}
  .icon{width:8px;height:8px;fill:var(--brand-blue);flex:none}
  .contact-line{display:flex;align-items:center;gap:5px}

  /* Letterhead */
  .letterhead{left:30px;top:30px;width:340px;height:480px;padding:34px 30px}
  .letterhead .brand{font-size:17px;position:absolute;left:30px;top:40px}
  .letterhead .sender{position:absolute;right:28px;top:30px;font-size:6.5px;line-height:1.45;color:var(--ink-soft)}
  .letterhead .sender .icon{width:6px;height:6px}
  .letter-body{position:absolute;left:30px;right:30px;top:110px;font-size:7.2px;line-height:1.5;font-weight:400;color:var(--ink)}
  .letter-body p{margin-bottom:9px}
  .letterhead .footer-bands{height:22px}

  /* Envelope back */
  .envelope{left:30px;top:540px;width:360px;height:185px}
  .envelope svg{position:absolute;inset:0;width:100%;height:100%}

  /* Desk calendar */
  .calendar{left:400px;top:30px;width:340px;height:500px;border-top:8px solid #3b3b3b}
  .calendar .photo{height:165px;background:linear-gradient(135deg,var(--photo-a),var(--photo-b))}
  .calendar .brand{position:absolute;right:14px;top:16px;font-size:12px}
  .calendar .top-band{height:14px;display:block}
  .year{font-family:"Poppins",Arial,sans-serif;font-weight:700;font-size:32px;color:var(--brand-blue);text-align:center;margin:8px 0 10px;letter-spacing:1px}
  .year span{color:var(--brand-teal)}
  .months{display:grid;grid-template-columns:repeat(4,1fr);gap:10px 10px;padding:0 16px}
  .month h4{font-family:"Poppins",Arial,sans-serif;font-weight:500;font-size:6.5px;color:#fff;text-align:center;padding:1px 0;margin-bottom:2px}
  .month.blue h4{background:var(--brand-blue)}
  .month.teal h4{background:var(--brand-teal)}
  .days{display:grid;grid-template-columns:repeat(7,1fr);font-size:5.6px;line-height:8px;text-align:center}
  .days b{font-weight:500;color:var(--ink-soft);font-size:4.6px}
  .days i{font-style:normal}
  .s2{grid-column-start:2}.s3{grid-column-start:3}.s4{grid-column-start:4}
  .s5{grid-column-start:5}.s6{grid-column-start:6}.s7{grid-column-start:7}
  .calendar .footer-bands{height:18px}

  /* Business cards */
  .card{width:300px;height:170px;left:770px}
  .card-front{top:30px;padding:0}
  .card-front .brand{position:absolute;left:22px;top:68px;font-size:15px}
  .card-front .divider{position:absolute;left:150px;top:44px;width:1px;height:78px;background:var(--brand-blue)}
  .card-front .holder{position:absolute;left:162px;top:44px;font-size:6.5px;line-height:1.5;color:var(--ink-soft)}
  .holder .name{font-family:"Poppins",Arial,sans-serif;font-weight:600;font-size:9px;color:var(--brand-blue);letter-spacing:.3px}
  .holder .role{font-size:7px;color:var(--brand-teal);margin-bottom:5px}
  .holder .icon{width:6px;height:6px}
  .card-front .footer-bands{height:18px}
  .card-back{top:220px;background:var(--brand-blue);display:flex;align-items:center;justify-content:center}
  .card-back .brand{font-size:20px;color:#8fb8e3}
  .card-back .brand::before{background:#8fb8e3}

  /* Compliment slip */
  .slip{left:420px;top:550px;width:750px;height:320px}
  .slip .brand{position:absolute;left:40px;top:46px;font-size:24px}
  .slip .crosses{position:absolute;right:70px;top:22px;width:260px;height:230px}
  .slip .address{position:absolute;left:44px;bottom:54px;font-size:10px;line-height:1.55;color:var(--ink)}
  .slip .address .icon{width:9px;height:9px}
  .slip .footer-bands{height:26px}
</style>
</head>
<body>

<svg width="0" height="0" style="position:absolute" aria-hidden="true">
  <symbol id="i-phone" viewBox="0 0 24 24"><path d="M6.6 10.8a15 15 0 0 0 6.6 6.6l2.2-2.2a1 1 0 0 1 1-.25 11.4 11.4 0 0 0 3.6.57 1 1 0 0 1 1 1V20a1 1 0 0 1-1 1A17 17 0 0 1 3 4a1 1 0 0 1 1-1h3.5a1 1 0 0 1 1 1c0 1.25.2 2.45.57 3.57a1 1 0 0 1-.25 1z"/></symbol>
  <symbol id="i-mail" viewBox="0 0 24 24"><path d="M2 5h20v14H2zM4 7v.4l8 5 8-5V7l-8 5z"/></symbol>
  <symbol id="i-web" viewBox="0 0 24 24"><path d="M12 2a10 10 0 1 0 0 20 10 10 0 0 0 0-20zm0 2c.9 1.2 1.6 2.6 2 4h-4c.4-1.4 1.1-2.8 2-4zM4.3 14a8 8 0 0 1 0-4h3.4a16 16 0 0 0 0 4zm.8 2h3c.3 1.3.8 2.5 1.4 3.6A8 8 0 0 1 5.1 16zm3-8h-3a8 8 0 0 1 4.4-3.6C8.900 5.5 8.4 6.7 8.1 8zM12 20c-.9-1.2-1.6-2.6-2-4h4c-.4 1.4-1.1 2.8-2 4zm2.3-6H9.7a14 14 0 0 1 0-4h4.6a14 14 0 0 1 0 4zm.2 5.6c.6-1.1 1.1-2.3 1.4-3.6h3a8 8 0 0 1-4.4 3.6zM16.3 14a16 16 0 0 0 0-4h3.4a8 8 0 0 1 0 4z"/></symbol>
  <symbol id="bands" viewBox="0 0 100 10" preserveAspectRatio="none">
    <polygon points="0,4 76,4 74,10 0,10" fill="#1e6fbf"/>
    <polygon points="78,3 100,3 100,7.5 76.6,7.5" fill="#1a9a8a"/>
  </symbol>
</svg>

<!-- Letterhead -->
<section class="sheet letterhead">
  <div class="brand">TORVALE MED</div>
  <address class="sender">
    Halden House, 42 Marlow Road<br>London SE4 1QT
    <div class="contact-line"><svg class="icon"><use href="#i-phone"/></svg>0204 555 0187</div>
    <div class="contact-line"><svg class="icon"><use href="#i-mail"/></svg>info@torvalemed.com</div>
    <div class="contact-line"><svg class="icon"><use href="#i-web"/></svg>www.torvalemed.com</div>
  </address>
  <div class="letter-body">
    <p>Dear customer,</p>
    <p>Lorem ipsum dolor sit amet, consectetur adipisicing elit, sed do eiusmod tempor incididunt ut labore et dolore magna aliqua. Ut enim ad minim veniam, quis nostrud exercitation ullamco laboris nisi ut aliquip ex ea commodo consequat. Duis aute irure dolor in reprehenderit in voluptate velit esse cillum dolore eu fugiat nulla pariatur. Excepteur sint occaecat cupidatat non proident, sunt in culpa qui officia deserunt mollit anim id est laborum.</p>
    <p>Lorem ipsum dolor sit amet, consectetur adipisicing elit, sed do eiusmod tempor incididunt ut labore et dolore magna aliqua. Ut enim ad minim veniam, quis nostrud exercitation ullamco laboris nisi ut aliquip ex ea commodo consequat. Duis aute irure dolor in reprehenderit in voluptate velit esse cillum dolore eu fugiat nulla pariatur. Excepteur sint occaecat cupidatat non proident, sunt in culpa qui officia deserunt mollit anim id est laborum.</p>
    <p>Lorem ipsum dolor sit amet, consectetur adipisicing elit, sed do eiusmod tempor incididunt ut labore et dolore magna aliqua. Ut enim ad minim veniam, quis nostrud exercitation ullamco laboris nisi ut aliquip ex ea commodo consequat. Duis aute irure dolor in reprehenderit in voluptate velit esse cillum dolore eu fugiat nulla pariatur. Excepteur sint occaecat cupidatat non proident, sunt in culpa qui officia deserunt mollit anim id est laborum.</p>
    <p>Lorem ipsum dolor sit amet, consectetur adipisicing elit, sed do eiusmod tempor incididunt ut labore et dolore magna aliqua. Ut enim ad minim veniam, quis nostrud exercitation ullamco laboris nisi ut aliquip ex ea commodo consequat. Duis aute irure dolor in reprehenderit.</p>
    <p>Yours Sincerely,</p>
  </div>
  <svg class="footer-bands"><use href="#bands"/></svg>
</section>

<!-- Envelope back -->
<section class="sheet envelope">
  <svg viewBox="0 0 360 185" preserveAspectRatio="none">
    <path d="M0 0 H360 V34 Q360 46 348 50 L30 82 Q0 86 0 60 Z" fill="#1e6fbf"/>
  </svg>
</section>

<!-- Desk calendar -->
<section class="sheet calendar">
  <div class="photo" role="img" aria-label="Photo of a clinician in a white coat preparing imaging equipment"></div>
  <div class="brand">TORVALE MED</div>
  <svg class="top-band" width="100%" height="14" viewBox="0 0 100 10" preserveAspectRatio="none">
    <polygon points="0,3 100,0 100,4 0,7" fill="#1e6fbf"/>
  </svg>
  <div class="year">202<span>3</span></div>
  <div class="months">
    <div class="month blue"><h4>January</h4><div class="days"><b>S</b><b>M</b><b>T</b><b>W</b><b>T</b><b>F</b><b>S</b><i>1</i><i>2</i><i>3</i><i>4</i><i>5</i><i>6</i><i>7</i><i>8</i><i>9</i><i>10</i><i>11</i><i>12</i><i>13</i><i>14</i><i>15</i><i>16</i><i>17</i><i>18</i><i>19</i><i>20</i><i>21</i><i>22</i><i>23</i><i>24</i><i>25</i><i>26</i><i>27</i><i>28</i><i>29</i><i>30</i><i>31</i></div></div>
    <div class="month teal"><h4>February</h4><div class="days"><b>S</b><b>M</b><b>T</b><b>W</b><b>T</b><b>F</b><b>S</b><i class="s4">1</i><i>2</i><i>3</i><i>4</i><i>5</i><i>6</i><i>7</i><i>8</i><i>9</i><i>10</i><i>11</i><i>12</i><i>13</i><i>14</i><i>15</i><i>16</i><i>17</i><i>18</i><i>19</i><i>20</i><i>21</i><i>22</i><i>23</i><i>24</i><i>25</i><i>26</i><i>27</i><i>28</i></div></div>
    <div class="month blue"><h4>March</h4><div class="days"><b>S</b><b>M</b><b>T</b><b>W</b><b>T</b><b>F</b><b>S</b><i class="s4">1</i><i>2</i><i>3</i><i>4</i><i>5</i><i>6</i><i>7</i><i>8</i><i>9</i><i>10</i><i>11</i><i>12</i><i>13</i><i>14</i><i>15</i><i>16</i><i>17</i><i>18</i><i>19</i><i>20</i><i>21</i><i>22</i><i>23</i><i>24</i><i>25</i><i>26</i><i>27</i><i>28</i><i>29</i><i>30</i><i>31</i></div></div>
    <div class="month teal"><h4>April</h4><div class="days"><b>S</b><b>M</b><b>T</b><b>W</b><b>T</b><b>F</b><b>S</b><i class="s7">1</i><i>2</i><i>3</i><i>4</i><i>5</i><i>6</i><i>7</i><i>8</i><i>9</i><i>10</i><i>11</i><i>12</i><i>13</i><i>14</i><i>15</i><i>16</i><i>17</i><i>18</i><i>19</i><i>20</i><i>21</i><i>22</i><i>23</i><i>24</i><i>25</i><i>26</i><i>27</i><i>28</i><i>29</i><i>30</i></div></div>
    <div class="month blue"><h4>May</h4><div class="days"><b>S</b><b>M</b><b>T</b><b>W</b><b>T</b><b>F</b><b>S</b><i class="s2">1</i><i>2</i><i>3</i><i>4</i><i>5</i><i>6</i><i>7</i><i>8</i><i>9</i><i>10</i><i>11</i><i>12</i><i>13</i><i>14</i><i>15</i><i>16</i><i>17</i><i>18</i><i>19</i><i>20</i><i>21</i><i>22</i><i>23</i><i>24</i><i>25</i><i>26</i><i>27</i><i>28</i><i>29</i><i>30</i><i>31</i></div></div>
    <div class="month teal"><h4>June</h4><div class="days"><b>S</b><b>M</b><b>T</b><b>W</b><b>T</b><b>F</b><b>S</b><i class="s5">1</i><i>2</i><i>3</i><i>4</i><i>5</i><i>6</i><i>7</i><i>8</i><i>9</i><i>10</i><i>11</i><i>12</i><i>13</i><i>14</i><i>15</i><i>16</i><i>17</i><i>18</i><i>19</i><i>20</i><i>21</i><i>22</i><i>23</i><i>24</i><i>25</i><i>26</i><i>27</i><i>28</i><i>29</i><i>30</i></div></div>
    <div class="month blue"><h4>July</h4><div class="days"><b>S</b><b>M</b><b>T</b><b>W</b><b>T</b><b>F</b><b>S</b><i class="s7">1</i><i>2</i><i>3</i><i>4</i><i>5</i><i>6</i><i>7</i><i>8</i><i>9</i><i>10</i><i>11</i><i>12</i><i>13</i><i>14</i><i>15</i><i>16</i><i>17</i><i>18</i><i>19</i><i>20</i><i>21</i><i>22</i><i>23</i><i>24</i><i>25</i><i>26</i><i>27</i><i>28</i><i>29</i><i>30</i><i>31</i></div></div>
    <div class="month teal"><h4>August</h4><div class="days"><b>S</b><b>M</b><b>T</b><b>W</b><b>T</b><b>F</b><b>S</b><i class="s3">1</i><i>2</i><i>3</i><i>4</i><i>5</i><i>6</i><i>7</i><i>8</i><i>9</i><i>10</i><i>11</i><i>12</i><i>13</i><i>14</i><i>15</i><i>16</i><i>17</i><i>18</i><i>19</i><i>20</i><i>21</i><i>22</i><i>23</i><i>24</i><i>25</i><i>26</i><i>27</i><i>28</i><i>29</i><i>30</i><i>31</i></div></div>
    <div class="month blue"><h4>September</h4><div class="days"><b>S</b><b>M</b><b>T</b><b>W</b><b>T</b><b>F</b><b>S</b><i class="s6">1</i><i>2</i><i>3</i><i>4</i><i>5</i><i>6</i><i>7</i><i>8</i><i>9</i><i>10</i><i>11</i><i>12</i><i>13</i><i>14</i><i>15</i><i>16</i><i>17</i><i>18</i><i>19</i><i>20</i><i>21</i><i>22</i><i>23</i><i>24</i><i>25</i><i>26</i><i>27</i><i>28</i><i>29</i><i>30</i></div></div>
    <div class="month teal"><h4>October</h4><div class="days"><b>S</b><b>M</b><b>T</b><b>W</b><b>T</b><b>F</b><b>S</b><i>1</i><i>2</i><i>3</i><i>4</i><i>5</i><i>6</i><i>7</i><i>8</i><i>9</i><i>10</i><i>11</i><i>12</i><i>13</i><i>14</i><i>15</i><i>16</i><i>17</i><i>18</i><i>19</i><i>20</i><i>21</i><i>22</i><i>23</i><i>24</i><i>25</i><i>26</i><i>27</i><i>28</i><i>29</i><i>30</i><i>31</i></div></div>
    <div class="month blue"><h4>November</h4><div class="days"><b>S</b><b>M</b><b>T</b><b>W</b><b>T</b><b>F</b><b>S</b><i class="s4">1</i><i>2</i><i>3</i><i>4</i><i>5</i><i>6</i><i>7</i><i>8</i><i>9</i><i>10</i><i>11</i><i>12</i><i>13</i><i>14</i><i>15</i><i>16</i><i>17</i><i>18</i><i>19</i><i>20</i><i>21</i><i>22</i><i>23</i><i>24</i><i>25</i><i>26</i><i>27</i><i>28</i><i>29</i><i>30</i></div></div>
    <div class="month teal"><h4>December</h4><div class="days"><b>S</b><b>M</b><b>T</b><b>W</b><b>T</b><b>F</b><b>S</b><i class="s6">1</i><i>2</i><i>3</i><i>4</i><i>5</i><i>6</i><i>7</i><i>8</i><i>9</i><i>10</i><i>11</i><i>12</i><i>13</i><i>14</i><i>15</i><i>16</i><i>17</i><i>18</i><i>19</i><i>20</i><i>21</i><i>22</i><i>23</i><i>24</i><i>25</i><i>26</i><i>27</i><i>28</i><i>29</i><i>30</i><i>31</i></div></div>
  </div>
  <svg class="footer-bands"><use href="#bands"/></svg>
</section>

<!-- Business card front -->
<section class="sheet card card-front">
  <div class="brand">TORVALE MED</div>
  <div class="divider"></div>
  <div class="holder">
    <div class="name">LENA M. OSTRANDER</div>
    <div class="role">Managing Director</div>
    Torvale Med Ltd<br>12 Harbour Row<br>Brackwell BW2 4LN
    <div class="contact-line"><svg class="icon"><use href="#i-phone"/></svg>0204 555 0187</div>
    <div class="contact-line"><svg class="icon"><use href="#i-mail"/></svg>info@torvalemed.com</div>
    <div class="contact-line"><svg class="icon"><use href="#i-web"/></svg>www.torvalemed.com</div>
  </div>
  <svg class="footer-bands"><use href="#bands"/></svg>
</section>

<!-- Business card back -->
<section class="sheet card card-back">
  <div class="brand">TORVALE MED</div>
</section>

<!-- Compliment slip -->
<section class="sheet slip">
  <div class="brand">TORVALE MED</div>
  <svg class="crosses" viewBox="0 0 260 230" aria-hidden="true">
    <rect x="40" y="0" width="70" height="70" fill="#e3e8ec"/>
    <rect x="165" y="50" width="85" height="75" fill="#e3e8ec"/>
    <rect x="0" y="80" width="170" height="150" fill="var(--cross-tint)"/>
  </svg>
  <address class="address">
    Halden House, 42 Marlow Road<br>London SE4 1QT
    <div class="contact-line"><svg class="icon"><use href="#i-phone"/></svg>0204 555 0187</div>
    <div class="contact-line"><svg class="icon"><use href="#i-mail"/></svg>info@torvalemed.com</div>
    <div class="contact-line"><svg class="icon"><use href="#i-web"/></svg>www.torvalemed.com</div>
  </address>
  <svg class="footer-bands"><use href="#bands"/></svg>
</section>

</body>
</html>
```